Telecommunications/Power civil contractor needs business card design

Were a new telecommunications/power underground civil contractor that is looking for a new business card design. Our company colours are silver or grey and orange. Feel free to use the white background logo or the black background logo.

Target Market(s)

Local contractors, utility companies, private sector mining/energy companies, developers.

Industry/Entity Type

Telecommunications

Contact Information for Business Card

Each card will need the following info:
Persons name:
Title:
E-mail:
Phone number:
Shop Address:
Mailing Address:

Requirements
Must have
• Each card will need the following info:
• Persons name:
• Title:
• E-mail:
• Phone number:
• Shop Address:
• Mailing Address:

```html
<!DOCTYPE html>
<html lang="en">
<head>
<meta charset="utf-8">
<title>Tamber Line Contracting Inc — Business Card</title>
<link href="https://fonts.googleapis.com/css2?family=Open+Sans:wght@400;600;700&display=swap" rel="stylesheet">
<style>
  :root {
    --orange: #f15a24;
    --grey: #7a7a7a;
    --grey-light: #a3a3a3;
    --white: #ffffff;
    --backdrop: #e9e7e4;
  }
  * { margin: 0; padding: 0; box-sizing: border-box; }
  html, body {
    width: 1200px;
    height: 900px;
    overflow: hidden;
    background: var(--backdrop);
    font-family: "Open Sans", Arial, sans-serif;
  }
  .card {
    position: absolute;
    left: 180px;
    top: 192px;
    width: 652px;
    height: 400px;
    transform: scale(1.2883);
    transform-origin: 0 0;
    background: var(--white);
    overflow: hidden;
    box-shadow: 0 6px 18px rgba(0,0,0,0.18);
  }
  .card-wave {
    position: absolute;
    inset: 0;
    width: 652px;
    height: 400px;
  }
  .brand {
    position: absolute;
    left: 68px;
    top: 44px;
    width: 210px;
    text-align: center;
  }
  .brand-mark {
    display: block;
    margin: 0 auto 10px;
  }
  .brand-name {
    color: var(--orange);
    font-weight: 700;
    font-size: 17px;
    line-height: 1.15;
    letter-spacing: 0.5px;
  }
  .contact {
    position: absolute;
    right: 27px;
    top: 150px;
    text-align: right;
    color: var(--white);
  }
  .contact-name {
    font-weight: 600;
    font-size: 22px;
    line-height: 1.2;
  }
  .contact-title {
    font-size: 16px;
    line-height: 1.2;
    margin-right: 4px;
  }
  .contact-line {
    display: flex;
    justify-content: flex-end;
    align-items: center;
    gap: 6px;
    font-size: 16px;
    line-height: 1.2;
  }
  .contact-phone { margin-top: 16px; }
  .contact-email { margin-top: 7px; }
  .icon { width: 13px; height: 13px; fill: var(--white); }
  .address-label {
    font-weight: 600;
    font-size: 19px;
    line-height: 1.2;
    margin-top: 14px;
  }
  .address-label.shop { margin-top: 6px; }
  .address-text {
    font-size: 16px;
    line-height: 1.2;
  }
</style>
</head>
<body>
  <div class="card">
    <svg class="card-wave" viewBox="0 0 652 400" aria-hidden="true">
      <path d="M0,179 C60,262 140,292 232,272 C332,252 422,92 522,87 C582,84 630,112 652,137 L652,400 L0,400 Z" fill="var(--orange)"/>
      <path d="M0,166 C60,250 140,282 232,262 C332,242 422,76 522,71 C582,68 630,98 652,124" fill="none" stroke="var(--grey)" stroke-width="7"/>
    </svg>

    <div class="brand">
      <svg class="brand-mark" width="96" height="96" viewBox="0 0 96 96" aria-hidden="true">
        <circle cx="48" cy="48" r="44" fill="none" stroke="var(--grey-light)" stroke-width="5"/>
      </svg>
      <div class="brand-name">TAMBER LINE<br>CONTRACTING INC</div>
    </div>

    <div class="contact">
      <div class="contact-name">Marcus Hale</div>
      <div class="contact-title">Managing Director</div>
      <div class="contact-line contact-phone">
        <span>(055)-321-6480</span>
        <svg class="icon" viewBox="0 0 24 24" aria-hidden="true"><path d="M6.6 10.8c1.4 2.8 3.8 5.1 6.6 6.6l2.2-2.2c.3-.3.7-.4 1-.2 1.1.4 2.3.6 3.6.6.6 0 1 .4 1 1V20c0 .6-.4 1-1 1C10.6 21 3 13.4 3 4c0-.6.4-1 1-1h3.5c.6 0 1 .4 1 1 0 1.3.2 2.5.6 3.6.1.3 0 .7-.2 1L6.6 10.8z"/></svg>
      </div>
      <div class="contact-line contact-email">
        <span>hello@tamberline.com</span>
        <svg class="icon" viewBox="0 0 24 24" aria-hidden="true"><path d="M2 5h20v14H2z M3.5 6.5 12 13l8.5-6.5" fill="none" stroke="#fff" stroke-width="2"/><path d="M2 5h20v14H2z"/><path d="M3 6l9 7 9-7" fill="none" stroke="var(--orange)" stroke-width="2"/></svg>
      </div>
      <div class="address-label">Mailing Address</div>
      <div class="address-text">12345, Address Goes Here Country Name, 123456</div>
      <div class="address-label shop">Shop Address</div>
      <div class="address-text">12345, Address Goes Here Country Name, 123456</div>
    </div>
  </div>
</body>
</html>
```